Fun, Clean Business Card For Family Focused Travel Agency

I need a business card using specific colors and fonts as in the uploaded files. Ideally, I would like a large image of the logo on the back and all the contact info on the front. Maybe the stars/dots somewhere in a flowy form.

I do want it the contact information to be clear and easy to read. I don't want it to look too busy. Maybe even a bit minimalist.

I plan or ordering the ROUNDED CORNER business cards from Cardwell Press, so please consider that in your design.

Target Market(s)

Families with children, couples, groups of friends

Contact Information for Business Card

Marla Quint, Owner
Marla@TumbleTrips.example
Cell Phone Number 555-218-4603
Office Phone Number 555-647-1925
Specializing in Glimmerland destinations, Pelican Bay Fun Park, Cruises and All-Inclusive Vacations.

Nice but not required:
www.TumbleTrips.example
Facebook, Instagram, Twitter icons with username: TumbleTrips

Font styles to use
Sans Serif

Requirements
Must have
• Please try to use the colors from the logo as much as possible. I understand lighter shades/colors may be needed for some things.
Should not have
• NO SERIF FONTS. That is really the only thing I do not want at all

```html
<!DOCTYPE html>
<html lang="en">
<head>
<meta charset="utf-8">
<title>Tumble Trips – Business Card</title>
<link rel="stylesheet" href="https://fonts.googleapis.com/css2?family=Ubuntu:wght@500;700&family=Open+Sans:wght@400;600&display=swap">
<style>
  :root {
    --navy: #13152a;
    --paper: #ffffff;
    --backdrop: #e8e9eb;
    --ink: #1c1d2b;
    --orange: #ee6a1c;
    --teal: #16b39a;
    --blue: #2a8fd6;
    --yellow: #d9a91c;
    --green: #7cc242;
    --muted: #5a5b66;
  }
  * { box-sizing: border-box; margin: 0; padding: 0; }
  html, body { width: 1200px; height: 900px; overflow: hidden; }
  body {
    background: var(--backdrop);
    display: flex;
    align-items: center;
    justify-content: center;
    gap: 40px;
    font-family: "Open Sans", Arial, sans-serif;
  }
  .card {
    position: relative;
    width: 540px;
    height: 309px;
    border-radius: 16px;
    overflow: hidden;
    box-shadow: 0 10px 24px rgba(20, 22, 40, 0.12);
  }
  .card--back { background: var(--navy); }
  .card--front { background: var(--paper); }

  .sprinkle { position: absolute; inset: 0; width: 100%; height: 100%; }

  /* back */
  .back-brand {
    position: absolute;
    left: 0; right: 0; top: 92px;
    display: flex; align-items: center; justify-content: center; gap: 14px;
  }
  .brand-dot {
    width: 46px; height: 46px; border-radius: 50%;
    background: var(--teal);
  }
  .brand-name {
    font-family: "Ubuntu", Arial, sans-serif;
    font-weight: 500;
    font-size: 56px;
    line-height: 1;
    color: var(--paper);
    letter-spacing: 0.5px;
  }
  .tagline {
    position: absolute;
    left: 0; right: 0; top: 190px;
    text-align: center;
    font-family: "Ubuntu", Arial, sans-serif;
    font-weight: 500;
    font-size: 14.5px;
    line-height: 1.45;
    color: var(--orange);
  }

  /* front */
  .front-brand {
    position: absolute; left: 34px; top: 104px;
    display: flex; align-items: center; gap: 10px;
  }
  .front-brand .brand-dot { width: 30px; height: 30px; }
  .front-brand .brand-name { font-size: 34px; color: var(--ink); }

  .divider {
    position: absolute; height: 1.5px;
  }
  .divider--orange { left: 34px; top: 162px; width: 250px; background: var(--orange); }
  .divider--blue { left: 284px; top: 162px; width: 0; }
  .name-rule { position: absolute; right: 34px; top: 74px; width: 150px; height: 1.5px; background: var(--blue); }

  .person {
    position: absolute; right: 34px; top: 48px;
    text-align: right;
    font-family: "Ubuntu", Arial, sans-serif;
  }
  .person-name {
    font-weight: 500; font-size: 17px; letter-spacing: 0.3px;
    color: var(--ink); text-transform: uppercase;
  }
  .person-name .first { color: var(--teal); }
  .person-role {
    margin-top: 8px;
    font-family: "Open Sans", Arial, sans-serif;
    font-size: 12.5px; color: var(--ink);
  }

  .contacts {
    position: absolute; left: 34px; top: 182px;
    list-style: none;
    display: flex; flex-direction: column; gap: 7px;
  }
  .contact {
    display: flex; align-items: center; gap: 10px;
    font-size: 13px; color: var(--ink);
  }
  .contact-icon {
    width: 19px; height: 19px; border-radius: 50%;
    display: flex; align-items: center; justify-content: center;
    flex: none;
  }
  .contact-icon svg { width: 11px; height: 11px; }
  .icon--mobile { background: var(--teal); }
  .icon--phone { background: var(--orange); }
  .icon--mail { background: var(--green); }
  .icon--web { background: var(--yellow); }
  .contact .accent { color: var(--teal); }
</style>
</head>
<body>

  <section class="card card--back" aria-label="Card back">
    <svg class="sprinkle" viewBox="0 0 540 309" aria-hidden="true">
      <circle cx="118" cy="92" r="3" fill="var(--orange)"/>
      <circle cx="132" cy="82" r="2" fill="var(--yellow)"/>
      <circle cx="106" cy="110" r="2" fill="var(--blue)"/>
      <circle cx="142" cy="156" r="2" fill="var(--green)"/>
      <circle cx="100" cy="140" r="1.6" fill="var(--yellow)"/>
      <path d="M124 126 l2 5 5 2 -5 2 -2 5 -2 -5 -5 -2 5 -2z" fill="var(--teal)"/>
      <path d="M408 80 l1.5 4 4 1.5 -4 1.5 -1.5 4 -1.5 -4 -4 -1.5 4 -1.5z" fill="var(--green)"/>
      <circle cx="426" cy="150" r="2" fill="var(--orange)"/>
    </svg>
    <div class="back-brand">
      <span class="brand-dot"></span>
      <span class="brand-name">Tumble Trips</span>
    </div>
    <p class="tagline">Specializing in Glimmerland destinations, Pelican Bay Fun Park<br>Cruises and All-Inclusive Vacations</p>
  </section>

  <section class="card card--front" aria-label="Card front">
    <svg class="sprinkle" viewBox="0 0 540 309" aria-hidden="true">
      <path d="M406 26 l3 8 8 3 -8 3 -3 8 -3 -8 -8 -3 8 -3z" fill="var(--blue)"/>
      <circle cx="470" cy="40" r="7" fill="var(--orange)"/>
      <circle cx="288" cy="54" r="7" fill="var(--orange)"/>
      <circle cx="340" cy="112" r="4" fill="var(--yellow)"/>
      <path d="M470 150 l3 8 8 3 -8 3 -3 8 -3 -8 -8 -3 8 -3z" fill="var(--blue)"/>
      <circle cx="506" cy="112" r="3" fill="var(--blue)"/>
      <path d="M506 140 l1.5 4 4 1.5 -4 1.5 -1.5 4 -1.5 -4 -4 -1.5 4 -1.5z" fill="var(--green)"/>
      <path d="M392 146 l1.5 4 4 1.5 -4 1.5 -1.5 4 -1.5 -4 -4 -1.5 4 -1.5z" fill="var(--green)"/>
      <circle cx="498" cy="204" r="4" fill="var(--yellow)"/>
      <circle cx="446" cy="92" r="2.5" fill="var(--green)"/>
      <line x1="284" y1="163" x2="506" y2="163" stroke="var(--blue)" stroke-width="1.5" opacity="0"/>
    </svg>

    <div class="person">
      <p class="person-name"><span class="first">Marla</span> Quint</p>
      <p class="person-role">Owner</p>
    </div>
    <span class="name-rule"></span>

    <div class="front-brand">
      <span class="brand-dot"></span>
      <span class="brand-name">Tumble Trips</span>
    </div>
    <span class="divider divider--orange"></span>

    <ul class="contacts">
      <li class="contact">
        <span class="contact-icon icon--mobile"><svg viewBox="0 0 12 12"><rect x="3.5" y="1" width="5" height="10" rx="1" fill="none" stroke="#fff" stroke-width="1.2"/><circle cx="6" cy="9.3" r="0.6" fill="#fff"/></svg></span>
        555 218 4603
      </li>
      <li class="contact">
        <span class="contact-icon icon--phone"><svg viewBox="0 0 12 12"><path d="M2.5 1.5 l2 0 1 2.5 -1.3 1 a6 6 0 0 0 2.8 2.8 l1 -1.3 2.5 1 0 2 a1 1 0 0 1 -1 1 A8.5 8.5 0 0 1 1.5 2.5 a1 1 0 0 1 1 -1z" fill="#fff"/></svg></span>
        555 647 1925
      </li>
      <li class="contact">
        <span class="contact-icon icon--mail"><svg viewBox="0 0 12 12"><rect x="1" y="2.5" width="10" height="7" rx="0.8" fill="none" stroke="#fff" stroke-width="1.2"/><path d="M1.5 3 L6 6.6 10.5 3" fill="none" stroke="#fff" stroke-width="1.2"/></svg></span>
        Marla@TumbleTrips.example
      </li>
      <li class="contact">
        <span class="contact-icon icon--web"><svg viewBox="0 0 12 12"><circle cx="6" cy="6" r="4.6" fill="none" stroke="#fff" stroke-width="1.1"/><ellipse cx="6" cy="6" rx="2" ry="4.6" fill="none" stroke="#fff" stroke-width="1"/><line x1="1.4" y1="6" x2="10.6" y2="6" stroke="#fff" stroke-width="1"/></svg></span>
        www.<span class="accent">TumbleTrips</span>.example
      </li>
    </ul>
  </section>

</body>
</html>
```